Business Card Design for Property Development Company Director

I am looking for a professional and unforgettable business card design for our Director of our Property Development Company.
Please see attached .pptx file to find out what information to include. You don't have to follow the exact format shown in the file - I am interested to see your creative flair using the information provided.

```html
<!DOCTYPE html>
<html lang="en">
<head>
<meta charset="utf-8">
<title>Halvern Property Group – Business Card</title>
<link rel="stylesheet" href="https://fonts.googleapis.com/css2?family=Roboto:wght@400;500;700&family=Roboto+Condensed:wght@700&display=swap">
<style>
  :root {
    --brand-blue: #2b4f9f;
    --brand-grey: #55565a;
    --text-grey: #5d5e62;
    --panel-grey: #ececec;
    --card-white: #f8f8f8;
    --backdrop: #e4e4e4;
  }
  * { margin: 0; padding: 0; box-sizing: border-box; }
  html, body { width: 1200px; height: 726px; overflow: hidden; }
  body {
    background: var(--backdrop);
    font-family: "Roboto", Arial, sans-serif;
    position: relative;
  }
  .card {
    position: absolute;
    top: 205px;
    width: 540px;
    height: 310px;
    background: var(--card-white);
    box-shadow: 0 6px 18px rgba(0,0,0,0.12);
    overflow: hidden;
  }
  .card--front { left: 40px; }
  .card--back { left: 620px; }

  .wordmark {
    font-family: "Roboto", Arial, sans-serif;
    font-weight: 700; color: var(--brand-grey);
    letter-spacing: 1px; line-height: 1;
  }
  .stripe { position: absolute; height: 10px; }

  /* Front */
  .tagline {
    position: absolute; top: 40px; left: 0; width: 100%;
    text-align: center; color: var(--brand-blue);
    font-size: 19px; line-height: 1.2;
  }
  .front-wordmark {
    position: absolute; top: 110px; left: 0; width: 100%;
    display: flex; justify-content: center; align-items: center; gap: 16px;
  }
  .brand-square { width: 56px; height: 56px; background: var(--brand-blue); }
  .front-wordmark .wordmark { font-size: 40px; }
  .front-wordmark .wordmark small { display: block; font-size: 19px; letter-spacing: 4px; margin-top: 4px; }
  .invite {
    position: absolute; top: 212px; left: 0; width: 100%;
    text-align: center; color: var(--text-grey); font-size: 14px;
  }
  .invite em { font-style: normal; color: var(--brand-blue); }
  .front-stripe-grey { left: 0; width: 50%; top: 272px; background: var(--brand-grey); }
  .front-stripe-blue { left: 50%; width: 50%; top: 272px; background: var(--brand-blue); }

  /* Back */
  .back-panel {
    position: absolute; top: 0; right: 0; width: 52%; height: 266px;
    background: var(--panel-grey);
  }
  .back-wordmark { position: absolute; top: 28px; right: 28px; }
  .back-wordmark .wordmark { font-size: 32px; }
  .back-wordmark .wordmark small { display: block; font-size: 15px; letter-spacing: 3px; margin-top: 3px; }
  .licence {
    position: absolute; top: 196px; right: 28px; text-align: right;
    font-size: 12.5px; color: var(--text-grey); line-height: 1.35;
  }
  .licence span { color: var(--brand-blue); }
  .back-stripe-blue { left: 52%; width: 48%; top: 266px; background: var(--brand-blue); }
  .back-stripe-grey { left: 0; width: 52%; top: 276px; background: var(--brand-grey); }
  .back-square {
    position: absolute; left: 34px; top: 40px;
    width: 48px; height: 48px; background: var(--brand-blue);
  }
  .person { position: absolute; left: 34px; top: 110px; }
  .person-name {
    font-family: "Roboto Condensed", "Arial Narrow", sans-serif;
    font-weight: 700; font-size: 22px; color: var(--brand-blue);
  }
  .person-role { font-size: 13px; color: var(--text-grey); margin: 2px 0 0 18px; }
  .contacts { list-style: none; position: absolute; left: 34px; top: 178px; }
  .contacts li {
    display: flex; align-items: center; gap: 10px;
    font-size: 15px; color: var(--text-grey); height: 23px;
  }
  .contacts svg { width: 13px; height: 13px; fill: var(--brand-blue); flex: none; }
</style>
</head>
<body>
  <section class="card card--front" aria-label="Card front">
    <p class="tagline">Property Development<br>&amp; Site Acquisition Specialists</p>
    <div class="front-wordmark">
      <span class="brand-square"></span>
      <div class="wordmark">HALVERN<small>PROPERTY GROUP</small></div>
    </div>
    <p class="invite">Ask me about our <em>INVESTMENT &amp; PARTNERSHIP</em> opportunities</p>
    <div class="stripe front-stripe-grey"></div>
    <div class="stripe front-stripe-blue"></div>
  </section>

  <section class="card card--back" aria-label="Card back">
    <div class="back-panel"></div>
    <div class="back-wordmark">
      <div class="wordmark">HALVERN<small>PROPERTY GROUP</small></div>
    </div>
    <p class="licence">Real Estate Lic:<br><span>1234567 &amp; 1234568</span></p>
    <div class="stripe back-stripe-blue"></div>
    <div class="stripe back-stripe-grey"></div>

    <span class="back-square"></span>
    <div class="person">
      <p class="person-name">Daniel Mercer</p>
      <p class="person-role">Director</p>
    </div>
    <ul class="contacts">
      <li><svg viewBox="0 0 16 16" aria-hidden="true"><path d="M3 1l3 3-2 2c1 2 3 4 5 5l2-2 3 3-2 3C7 15 1 9 1 3z"/></svg>0400 123 456</li>
      <li><svg viewBox="0 0 16 16" aria-hidden="true"><path d="M1 3h14v10H1z M1 3l7 6 7-6" fill="none" stroke="#2b4f9f" stroke-width="1.6"/></svg>daniel@halvern.com.au</li>
      <li><svg viewBox="0 0 16 16" aria-hidden="true"><circle cx="8" cy="8" r="7"/><path d="M1 8h14M8 1c-3 4-3 10 0 14M8 1c3 4 3 10 0 14" fill="none" stroke="#f8f8f8" stroke-width="1"/></svg>www.halvern.com.au</li>
    </ul>
  </section>
</body>
</html>
```